Velundra Jobs portal

Velundra Jobs is a job portal connecting job seekers and companies offering part time jobs in the Mena region, starting in the UAE. We would like to see designs that use the color blue. We have attached images to give an idea what the website should look like. When a company posts a job the job seekers are not allowed to see which company has posted a job. There should also be a coinvex gateway. On the landing page we want a catching picture that we will send.

Target Market(s)

Students and promotional workers

Logo Text

Velundra Jobs

Coding

Coded - Design and coding required

Number of Pages Required

4 page

Font styles to use
Sans Serif

Colors
33a6d7
0692cd
85cae6

```html
<!DOCTYPE html>
<html lang="en">
<head>
<meta charset="utf-8">
<title>Velundra Jobs</title>
<link rel="stylesheet" href="https://fonts.googleapis.com/css2?family=Raleway:wght@300;500;800&family=Open+Sans:wght@400&display=swap">
<style>
  :root {
    --blue-main: #0692cd;
    --blue-mid: #33a6d7;
    --blue-light: #85cae6;
    --btn-blue-top: #4aaedb;
    --btn-blue-bottom: #2a86b8;
    --btn-pink-top: #e2679c;
    --btn-pink-bottom: #c2407a;
    --white: #ffffff;
    --photo-dark: #2e3036;
    --photo-mid: #74767c;
    --photo-light: #b9bbbf;
  }
  * { margin: 0; padding: 0; box-sizing: border-box; }
  html, body { width: 1200px; height: 668px; overflow: hidden; }
  body { position: relative; font-family: 'Raleway', sans-serif; color: var(--white); background: var(--photo-mid); }

  .hero-photo {
    position: absolute; left: 0; top: 0; width: 1200px; height: 603px;
    background:
      radial-gradient(ellipse 230px 320px at 370px 430px, var(--photo-dark) 0%, rgba(46,48,54,0.6) 55%, rgba(46,48,54,0) 100%),
      radial-gradient(ellipse 200px 280px at 1020px 360px, rgba(150,140,130,0.5) 0%, rgba(150,140,130,0) 100%),
      linear-gradient(180deg, var(--photo-light) 0%, var(--photo-mid) 60%, #5b5d63 100%);
  }
  .hero-shade { position: absolute; left: 0; top: 0; width: 1200px; height: 603px; background: rgba(40,42,48,0.35); }

  .brand { position: absolute; left: 99px; top: 98px; display: flex; align-items: center; gap: 6px; }
  .brand-dot { width: 14px; height: 14px; border-radius: 50%; background: var(--blue-light); }
  .brand-name { font-weight: 500; font-size: 26px; color: var(--blue-light); letter-spacing: 0.5px; }

  .top-nav { position: absolute; right: 94px; top: 57px; display: flex; align-items: center; gap: 8px; }
  .social-link { width: 31px; height: 31px; border-radius: 50%; background: var(--white); display: block; }
  .menu-toggle { margin-left: 11px; width: 24px; height: 20px; display: flex; flex-direction: column; justify-content: space-between; }
  .menu-toggle span { height: 4px; background: var(--white); border-radius: 1px; }

  .hero-copy { position: absolute; right: 99px; top: 290px; text-align: right; }
  .hero-title { font-weight: 800; font-size: 35px; letter-spacing: 0.3px; line-height: 1; }
  .hero-subtitle { font-weight: 300; font-size: 25px; margin-top: 17px; line-height: 1; }

  .hero-actions { position: absolute; right: 100px; top: 399px; display: flex; gap: 14px; }
  .btn { width: 142px; height: 51px; display: flex; align-items: center; justify-content: center; font-weight: 500; font-size: 16px; color: var(--white); text-decoration: none; border-radius: 2px; }
  .btn-join { width: 166px; background: linear-gradient(180deg, var(--btn-blue-top), var(--btn-blue-bottom)); }
  .btn-employer { background: linear-gradient(180deg, var(--btn-blue-top), var(--btn-blue-bottom)); }
  .btn-seeker { background: linear-gradient(180deg, var(--btn-pink-top), var(--btn-pink-bottom)); }

  .site-footer { position: absolute; left: 0; top: 603px; width: 1200px; height: 65px; background: var(--blue-main); }
  .footer-note { position: absolute; left: 99px; top: 25px; font-family: 'Open Sans', sans-serif; font-size: 11px; }
  .footer-actions { position: absolute; right: 99px; top: 14px; display: flex; gap: 7px; }
  .footer-icon { width: 36px; height: 36px; border-radius: 50%; border: 1px solid var(--white); display: flex; align-items: center; justify-content: center; }
</style>
</head>
<body>
  <div class="hero-photo" role="img" aria-label="Photo of a businessman in a suit in the foreground with blurred colleagues in an office behind him"></div>
  <div class="hero-shade"></div>

  <header>
    <div class="brand">
      <span class="brand-dot"></span>
      <span class="brand-name">velundra</span>
    </div>
    <nav class="top-nav">
      <a class="social-link" href="#" aria-label="Social page"></a>
      <a class="social-link" href="#" aria-label="Social page"></a>
      <a class="social-link" href="#" aria-label="Social page"></a>
      <div class="menu-toggle" aria-label="Menu"><span></span><span></span><span></span></div>
    </nav>
  </header>

  <main>
    <div class="hero-copy">
      <h1 class="hero-title">NUMBER ONE PLATFORM CONNECTING</h1>
      <p class="hero-subtitle">PEOPLE WITH EVENTS COMPANIES</p>
    </div>
    <div class="hero-actions">
      <a class="btn btn-join" href="#">JOIN VELUNDRA</a>
      <a class="btn btn-employer" href="#">EMPLOYER</a>
      <a class="btn btn-seeker" href="#">JOB SEEKER</a>
    </div>
  </main>

  <footer class="site-footer">
    <p class="footer-note">Copyrights©Velundra.2015. &nbsp; Allrights Reserved</p>
    <div class="footer-actions">
      <a class="footer-icon" href="#" aria-label="Email">
        <svg width="14" height="11" viewBox="0 0 14 11"><rect x="0" y="0" width="14" height="11" rx="1.5" fill="#fff"/><path d="M1 1.5 L7 6 L13 1.5" stroke="#0692cd" stroke-width="1.3" fill="none"/></svg>
      </a>
      <a class="footer-icon" href="#" aria-label="Back to top">
        <svg width="14" height="14" viewBox="0 0 14 14"><circle cx="7" cy="7" r="7" fill="#fff"/><path d="M7 11 V4 M4 7 L7 4 L10 7" stroke="#0692cd" stroke-width="1.8" fill="none" stroke-linecap="round"/></svg>
      </a>
    </div>
  </footer>
</body>
</html>
```